Quillfern Vaults - Direct Mailer / Flyer

We are excited to announce the launch of our new company, Quillfern Vaults, a premier cohosting facility and data center dedicated to Cryptocurrency Miners. Our website, https://quillfernvaults.example, provides detailed information about our offerings and showcases the innovative design schemes for the entire project.

Quillfern Vaults stands out in the industry by offering both GPU Hosting and ASIC Hosting services in our state-of-the-art facility, equipped with an impressive 17 Megawatts of available power. What sets us apart is our unique billing system based on actual metered power usage. We charge $0.08 for ASIC miners and $0.09 for GPU miners, ensuring cost-effectiveness and transparency for our clients.

Our commitment to excellence is evident in our use of cutting-edge technology, top-notch facilities, and strategic partnerships. These elements come together to deliver exceptional solutions tailored for real-world applications in the cryptocurrency space.

As part of our promotional efforts, we are developing a direct mailer/flyer to introduce Quillfern Vaults to a wider audience. This promotional material will also serve as a handout at events, to potential customers, and more. We welcome creative ideas and suggestions to maximize the versatility of this design and reach diverse target audiences effectively.

For a comprehensive overview of our services and to explore our design concepts, please visit https://quillfernvaults.example. Quillfern Vaults is poised to revolutionize the mining industry, and we look forward to partnering with you for success in the digital currency era.

```html
<!DOCTYPE html>
<html lang="en">
<head>
<meta charset="utf-8">
<title>Quillfern Vaults – Flyer</title>
<link href="https://fonts.googleapis.com/css2?family=Poppins:wght@400;500;600;700;800&display=swap" rel="stylesheet">
<style>
:root{
  --blue:#3355f0;
  --orange:#f7a313;
  --ink:#1f2226;
  --slate:#555b63;
  --charcoal:#2e3238;
  --paper:#ffffff;
  --mist:#eef1f6;
  --rule:#dfe2e7;
}
*{box-sizing:border-box;margin:0;padding:0}
html,body{width:850px;height:1200px;overflow:hidden;background:var(--paper)}
body{font-family:"Poppins",sans-serif;color:var(--ink);position:relative}
.flyer{position:relative;width:850px;height:1200px;overflow:hidden;background:var(--paper)}

.hero-art{position:absolute;left:430px;top:0;width:420px;height:450px;
  background:linear-gradient(160deg,#f3f5fa 0%,#dfe5f3 45%,#c9d2ec 70%,#ffffff 100%)}
.hero-art::after{content:"";position:absolute;left:150px;top:0;width:12px;height:120px;background:var(--blue);opacity:.85}

.brand{position:absolute;left:58px;top:66px;display:flex;align-items:center;gap:12px}
.brand-mark{width:30px;height:30px;background:var(--ink)}
.brand-name{font-weight:800;font-size:28px;letter-spacing:1px;color:var(--ink);text-transform:uppercase;line-height:1}

.headline{position:absolute;left:56px;top:138px;line-height:.95}
.headline .line-one{display:block;font-weight:500;font-size:64px;color:var(--ink);letter-spacing:1px}
.headline .line-two{display:block;font-weight:800;font-size:76px;color:var(--blue);letter-spacing:1px}

.tagline{position:absolute;left:58px;top:322px;font-weight:700;font-size:24px;line-height:1.3;color:var(--ink)}
.tagline .accent{color:var(--orange)}

.intro{position:absolute;left:58px;top:462px;width:384px;padding-left:22px;font-size:12.8px;line-height:1.36;color:var(--ink)}
.intro::before{content:"";position:absolute;left:0;top:4px;width:5px;height:94px;border-radius:3px;background:var(--orange)}

.rates{position:absolute;left:462px;top:455px;width:330px;text-align:center}
.rate-row{display:flex;align-items:flex-end;justify-content:space-between}
.rate{display:flex;flex-direction:column;align-items:center}
.rate-value{font-weight:800;font-size:28px;color:var(--blue);line-height:1}
.rate-label{margin-top:3px;background:var(--orange);color:var(--ink);font-size:12px;padding:1px 12px;border-radius:10px}
.rate-divider{font-weight:700;font-size:14px;line-height:1.05;margin-bottom:6px}
.rate-note{margin-top:12px;font-size:13px;line-height:1.3}

.services{position:absolute;left:60px;top:640px;display:flex;gap:32px}
.service{position:relative;width:158px;height:200px;border-radius:16px;color:#fff;text-align:center;padding:58px 12px 0;box-shadow:0 4px 0 #c9ced6}
.service.tone-slate{background:var(--slate)}
.service.tone-dark{background:var(--charcoal)}
.service-icon{position:absolute;left:50%;top:-30px;transform:translateX(-50%);width:64px;height:64px;border-radius:50%;background:var(--orange);border:5px solid #fff;display:flex;align-items:center;justify-content:center;box-shadow:0 0 0 2px var(--mist)}
.service h3{font-size:15px;font-weight:700;line-height:1.15;margin-bottom:8px}
.service p{font-size:11.6px;line-height:1.3}

.perks{position:absolute;left:60px;top:900px;display:grid;grid-template-columns:152px 152px;row-gap:26px}
.perk{display:flex;align-items:center;gap:12px;font-size:13.5px;line-height:1.2;height:64px}
.perk:nth-child(odd){border-right:1px solid var(--rule)}
.perk:nth-child(even){padding-left:20px}
.perk:nth-child(-n+2){border-bottom:1px solid var(--rule)}
.perks-divider{position:absolute;left:370px;top:890px;width:1px;height:180px;background:var(--rule)}

.commitment{position:absolute;left:394px;top:890px;width:410px}
.commitment p{font-size:12.4px;line-height:1.3}
.commitment .closing{margin-top:18px;font-size:18.5px;line-height:1.25;font-weight:400}
.commitment .closing b{font-weight:700}
.commitment .closing .brand-ref{color:var(--blue);font-weight:700}

.footer{position:absolute;left:0;top:1115px;width:850px;height:85px}
.contact-pill{position:absolute;left:40px;top:18px;width:380px;height:40px;border-radius:20px;background:var(--charcoal);color:#fff;display:flex;align-items:center;gap:18px;padding-left:18px;font-size:13px;white-space:nowrap}
.contact-pill span{display:flex;align-items:center;gap:5px}
.web-band{position:absolute;left:432px;top:0;width:418px;height:70px;background:var(--blue);border-top-left-radius:40px;color:#fff;display:flex;align-items:center;justify-content:center;font-size:22px;letter-spacing:1px}
.web-band b{font-weight:700}
.base-line{position:absolute;left:0;bottom:0;width:850px;height:15px;background:var(--blue)}
</style>
</head>
<body>
<main class="flyer">

  <div class="hero-art" role="img" aria-label="Illustration of a miner with a pickaxe striking a coin embedded in a rock, over glowing blue circuit lines"></div>

  <div class="brand">
    <div class="brand-mark"></div>
    <div class="brand-name">Quillfern Vaults</div>
  </div>

  <h1 class="headline">
    <span class="line-one">QUILLFERN</span>
    <span class="line-two">VAULTS</span>
  </h1>

  <p class="tagline">A premier cohosting facility<br>and data center dedicated to<br><span class="accent">Cryptocurrency Miners</span></p>

  <p class="intro">Quillfern Vaults stands out in the industry by offering both GPU Hosting and ASIC Hosting services in our state-of-the-art facility, equipped with an impressive 17 Megawatts of available power. What sets us apart is our unique billing system based on actual metered power usage.</p>

  <section class="rates">
    <div class="rate-row">
      <div class="rate"><span class="rate-value">$0.08</span><span class="rate-label">ASIC miners</span></div>
      <div class="rate-divider">WE<br>CHARGE</div>
      <div class="rate"><span class="rate-value">$0.09</span><span class="rate-label">GPU miners</span></div>
    </div>
    <p class="rate-note">ensuring cost-effectiveness &amp; transparency<br>for our clients.</p>
  </section>

  <section class="services">
    <article class="service tone-slate">
      <div class="service-icon">
        <svg width="30" height="30" viewBox="0 0 30 30" fill="none" stroke="#1f2226" stroke-width="2"><rect x="7" y="7" width="16" height="16" rx="2"/><rect x="11" y="11" width="8" height="8"/><path d="M11 3v4M15 3v4M19 3v4M11 23v4M15 23v4M19 23v4M3 11h4M3 15h4M3 19h4M23 11h4M23 15h4M23 19h4"/></svg>
      </div>
      <h3>GPU Hosting</h3>
      <p>Begin your GPU Hosting journey with rates starting at $0.09 kWh, accepting all equipment.</p>
    </article>
    <article class="service tone-dark">
      <div class="service-icon">
        <svg width="30" height="30" viewBox="0 0 30 30" fill="none" stroke="#1f2226" stroke-width="2"><rect x="8" y="8" width="14" height="14"/><path d="M11 19l8-8M15 3v5M15 22v5M3 15h5M22 15h5M6 6l3 3M24 6l-3 3M6 24l3-3M24 24l-3-3"/></svg>
      </div>
      <h3>ASIC Hosting</h3>
      <p>Get your ASICs directly from us or send yours in today, starting at an all-in rate of $0.08 kWh.</p>
    </article>
    <article class="service tone-slate">
      <div class="service-icon">
        <svg width="30" height="30" viewBox="0 0 30 30" fill="none" stroke="#1f2226" stroke-width="2"><rect x="5" y="5" width="16" height="6" rx="1"/><rect x="5" y="13" width="16" height="6" rx="1"/><rect x="5" y="21" width="10" height="5" rx="1"/><path d="M18 22l7 5M25 20v7h-7"/></svg>
      </div>
      <h3>Mining Hardware</h3>
      <p>Looking for mining hardware? Our equipment comes with no additional markup, ever.</p>
    </article>
    <article class="service tone-dark">
      <div class="service-icon">
        <svg width="30" height="30" viewBox="0 0 30 30" fill="none" stroke="#1f2226" stroke-width="2"><circle cx="15" cy="15" r="11"/><circle cx="15" cy="15" r="6"/></svg>
      </div>
      <h3>Crypto<br>Consulting</h3>
      <p>Enjoy complete White Glove Services for setup, insurance, and tax consulting.</p>
    </article>
  </section>

  <section class="perks">
    <div class="perk">
      <svg width="38" height="38" viewBox="0 0 38 38"><circle cx="19" cy="19" r="13" fill="none" stroke="#f7a313" stroke-width="3" stroke-dasharray="4 3"/><rect x="13" y="17" width="12" height="10" rx="1" fill="#f7a313"/><path d="M15 17v-3a4 4 0 0 1 8 0v3" fill="none" stroke="#f7a313" stroke-width="2.5"/></svg>
      <span>New<br>Secure<br>Facility</span>
    </div>
    <div class="perk">
      <svg width="38" height="38" viewBox="0 0 38 38" fill="none" stroke="#f7a313" stroke-width="3"><path d="M5 14a20 20 0 0 1 28 0M10 19a13 13 0 0 1 18 0"/><rect x="12" y="23" width="14" height="11" fill="#f7a313" stroke="none"/></svg>
      <span>24/7<br>Remote<br>Access</span>
    </div>
    <div class="perk">
      <svg width="38" height="38" viewBox="0 0 38 38"><g fill="#f7a313"><rect x="5" y="24" width="5" height="10"/><rect x="12" y="19" width="5" height="15"/><rect x="19" y="22" width="5" height="12"/><rect x="26" y="14" width="5" height="20"/></g><path d="M5 18l9-7 6 5 11-10" fill="none" stroke="#f7a313" stroke-width="2.5"/></svg>
      <span>99.45%<br>Uptime</span>
    </div>
    <div class="perk">
      <svg width="38" height="38" viewBox="0 0 38 38"><path d="M32 6c-10 1-16 7-20 15l5 5c8-4 14-10 15-20z" fill="#f7a313"/><path d="M12 21l-6 1 5-7 6-1zM17 26l-1 6 7-5 1-6z" fill="#f7a313"/><path d="M9 27l-4 6 6-4" fill="none" stroke="#f7a313" stroke-width="2"/></svg>
      <span>Speedy<br>Support</span>
    </div>
  </section>
  <div class="perks-divider"></div>

  <section class="commitment">
    <p>Our commitment to excellence is evident in our use of cutting-edge technology, top-notch facilities, and strategic partnerships. These elements come together to deliver exceptional solutions tailored for real-world applications in the cryptocurrency space.</p>
    <p class="closing"><span class="brand-ref">Quillfern Vaults</span> <b>is poised to revolutionize the mining industry,</b> and we look forward to partnering with you for success in the digital currency era</p>
  </section>

  <footer class="footer">
    <div class="contact-pill">
      <span><svg width="13" height="13" viewBox="0 0 24 24"><path d="M6 2l4 4-2 3a12 12 0 0 0 7 7l3-2 4 4-3 4C10 22 2 14 2 5z" fill="#f7a313"/></svg>555 0142 3086</span>
      <span><svg width="14" height="11" viewBox="0 0 24 18"><rect x="1" y="1" width="22" height="16" fill="#f7a313"/><path d="M1 1l11 9 11-9" fill="none" stroke="#2e3238" stroke-width="2"/></svg>hello@quillfernvaults.example</span>
    </div>
    <div class="web-band">www.<b>quillfernvaults</b>.example</div>
    <div class="base-line"></div>
  </footer>

</main>
</body>
</html>
```